Business Card Design For A Renovation Contractor Company

We need a business card for a new company based in Singapore, our company name is "RB Tolvane". We are a renovation contractor that builds designs into reality. We build more of F&B restaurants, retail stores and commercial offices. We work very closely with designers. The final design should communicate to our client that we are a company that you can trust, that will plan and complete your project without giving you a headache. I like my client to remember my company as "RB". The beauty of SIMPLE is important.

Industry/Entity Type

Contractor

Requirements
Nice to have
• Black or Red base

```html
<!DOCTYPE html>
<html lang="en">
<head>
<meta charset="utf-8">
<title>RB Tolvane – Business Cards</title>
<link href="https://fonts.googleapis.com/css2?family=Open+Sans:wght@400;600&family=Questrial&display=swap" rel="stylesheet">
<style>
  :root {
    --stage: #3b2b23;
    --red: #ec1c24;
    --ink: #1d1d1d;
    --mist: #eef1f2;
    --white: #ffffff;
    --black-card-1: #2a2a2a;
    --black-card-2: #0c0c0c;
    --label: #f2ece6;
  }
  * { box-sizing: border-box; margin: 0; padding: 0; }
  html, body { width: 1200px; height: 913px; overflow: hidden; }
  body {
    background: var(--stage);
    position: relative;
    font-family: "Open Sans", Arial, sans-serif;
  }
  .card {
    position: absolute;
    width: 463px;
    height: 265px;
    overflow: hidden;
    box-shadow: 0 3px 10px rgba(0,0,0,.45);
  }
  .card--front  { left: 91px;  top: 146px; background: var(--white); }
  .card--black  { left: 584px; top: 141px; width: 470px; background: linear-gradient(135deg, var(--black-card-1), var(--black-card-2) 60%, #222); }
  .card--red    { left: 91px;  top: 437px; background: var(--red); }
  .card--white  { left: 591px; top: 434px; background: var(--white); }

  .side-label {
    position: absolute;
    font-size: 28px;
    color: var(--label);
  }
  .side-label--1 { left: 946px; top: 92px; }
  .side-label--2 { left: 128px; top: 735px; }
  .side-label--3 { left: 981px; top: 731px; }

  /* brand lockup */
  .brand {
    position: absolute;
    display: flex;
    flex-direction: column;
    align-items: center;
    font-family: "Questrial", "Century Gothic", sans-serif;
  }
  .brand__circle {
    width: 58px; height: 58px;
    border-radius: 50%;
    border: 7px solid var(--red);
    margin-bottom: 8px;
  }
  .brand__name { font-size: 40px; line-height: 1; letter-spacing: -.5px; }
  .brand__tagline { font-size: 13px; margin-top: 3px; padding-top: 1px; border-top: 1px solid currentColor; }

  .card--front .brand { right: 22px; top: 24px; }
  .card--front .brand__circle { width: 62px; height: 62px; }
  .card--front .brand__name { color: var(--ink); font-size: 38px; }
  .card--front .brand__tagline { color: var(--ink); }

  .card--black .brand { left: 0; right: 0; top: 60px; }
  .card--black .brand__name, .card--black .brand__tagline { color: var(--white); }

  .card--red .brand { left: 0; right: 0; top: 46px; }
  .card--red .brand__circle { width: 80px; height: 80px; border-color: var(--white); }
  .card--red .brand__name { color: var(--white); font-size: 46px; }
  .card--red .brand__tagline { color: var(--white); font-size: 15px; }

  .card--white .brand { left: 0; right: 0; top: 62px; }
  .card--white .brand__name, .card--white .brand__tagline { color: var(--ink); }

  /* contact block */
  .contact {
    position: absolute;
    left: 33px; top: 28px;
    font-size: 11px;
    color: #333;
    line-height: 16px;
    list-style: none;
  }
  .contact li { display: flex; align-items: center; gap: 6px; }
  .contact svg { width: 11px; height: 11px; }
  .address {
    position: absolute;
    left: 33px; top: 98px;
    font-size: 11px;
    line-height: 15px;
    color: #333;
    font-style: normal;
  }
  .front-band {
    position: absolute;
    left: 0; right: 0; bottom: 0;
    height: 110px;
    background: linear-gradient(to bottom, var(--mist) 0%, #c9c9c9 22%, var(--red) 48%, var(--red) 100%);
  }
  .holder {
    position: absolute;
    left: 33px; bottom: 17px;
    color: var(--white);
    font-size: 22px;
  }
  .holder__role { font-size: 14px; }
</style>
</head>
<body>

<span class="side-label side-label--1">Back 1</span>
<span class="side-label side-label--2">Back 2</span>
<span class="side-label side-label--3">Back 3</span>

<section class="card card--front" aria-label="Card front">
  <ul class="contact">
    <li><svg viewBox="0 0 12 12"><path d="M3 1l2 2.5-1.2 1.2a7 7 0 0 0 3.5 3.5L8.5 7 11 9l-1 2C5 11 1 7 1 2z" fill="#333"/></svg>012.555.0189</li>
    <li><svg viewBox="0 0 12 12"><rect x="1" y="2.5" width="10" height="7" fill="#333"/><path d="M1 2.5l5 4 5-4" stroke="#fff" fill="none"/></svg>info@rbtolvane.com</li>
    <li><svg viewBox="0 0 12 12"><circle cx="6" cy="6" r="5" fill="none" stroke="#333" stroke-width="1.3"/><path d="M1 6h10M6 1c-3 3-3 7 0 10M6 1c3 3 3 7 0 10" stroke="#333" fill="none"/></svg>www.rbtolvane.com</li>
  </ul>
  <address class="address">Suite 000, RB building,<br>Cityname, country name</address>

  <div class="brand">
    <span class="brand__circle"></span>
    <span class="brand__name">RB Tolvane</span>
    <span class="brand__tagline">from plan to finished space</span>
  </div>

  <div class="front-band" role="img" aria-label="Decorative flowing band in red, grey and black across the lower card"></div>
  <p class="holder">Your name, <span class="holder__role">Director</span></p>
</section>

<section class="card card--black" aria-label="Card back, black">
  <div class="brand">
    <span class="brand__circle"></span>
    <span class="brand__name">RB Tolvane</span>
    <span class="brand__tagline">from plan to finished space</span>
  </div>
</section>

<section class="card card--red" aria-label="Card back, red">
  <div class="brand">
    <span class="brand__circle"></span>
    <span class="brand__name">RB Tolvane</span>
    <span class="brand__tagline">from plan to finished space</span>
  </div>
</section>

<section class="card card--white" aria-label="Card back, white">
  <div class="brand">
    <span class="brand__circle"></span>
    <span class="brand__name">RB Tolvane</span>
    <span class="brand__tagline">from plan to finished space</span>
  </div>
</section>

</body>
</html>
```